Local fast-growing company in the service sector

We are looking for a modern business card design, which should also appear on our letterheads

Target Market(s)

Private and industrial sectors

Contact Information for Business Card

Vorname Name
Kellberger Str. 18
71409 Kernbach
Tel.: 07146-839214-0
Name@agentur-kvtl.de

Colors
9d9d9d
919191
aaaaaa

Requirements
Must have
• The logo (file) in silver

```html
<!DOCTYPE html>
<html lang="de">
<head>
<meta charset="utf-8">
<title>KVTL – Visitenkarte</title>
<link rel="stylesheet" href="https://fonts.googleapis.com/css2?family=Open+Sans:wght@400;600;700&display=swap">
<style>
  :root {
    --stage: #e9e7e4;
    --card-white: #ffffff;
    --band-dark: #4f5052;
    --band-light: #aaaaaa;
    --brand-grey: #9d9d9d;
    --brand-grey-dark: #7d7d7d;
    --silver-light: #e6e6e6;
    --silver-mid: #aaaaaa;
    --silver-dark: #6f7072;
    --text-light: #ffffff;
  }
  * { margin: 0; padding: 0; box-sizing: border-box; }
  html, body { width: 1200px; height: 900px; overflow: hidden; }
  body {
    background: var(--stage);
    font-family: "Open Sans", Arial, sans-serif;
    position: relative;
  }
  .card {
    position: absolute;
    overflow: hidden;
    box-shadow: 0 4px 14px rgba(0,0,0,0.18);
  }
  /* Front side */
  .card-front {
    left: 178px; top: 73px; width: 588px; height: 364px;
    background: var(--card-white);
  }
  .front-bands { position: absolute; left: 0; top: 0; }
  .brand-mark {
    position: absolute;
    display: flex; align-items: center; gap: 18px;
    color: var(--brand-grey);
    font-weight: 700;
    letter-spacing: 2px;
    white-space: nowrap;
  }
  .card-front .brand-mark { left: 118px; top: 60px; font-size: 72px; }
  .brand-square {
    width: 62px; height: 62px;
    background: var(--brand-grey);
  }
  .holder-name {
    position: absolute; left: 100px; top: 268px;
    color: var(--text-light); font-weight: 700; font-size: 19px;
    white-space: nowrap;
  }
  .contact-list {
    position: absolute; left: 284px; top: 247px;
    list-style: none; color: var(--text-light); font-size: 16px;
  }
  .contact-list li {
    display: flex; align-items: center; gap: 7px;
    height: 21.5px; white-space: nowrap;
  }
  .contact-list svg { width: 12px; height: 12px; flex: none; }
  .address {
    position: absolute; left: 0; right: 0; top: 319px;
    text-align: center; color: var(--text-light); font-size: 15.5px;
    white-space: nowrap;
  }
  /* Back side */
  .card-back {
    left: 388px; top: 505px; width: 567px; height: 352px;
    background: linear-gradient(150deg, var(--silver-dark) 0%, var(--silver-mid) 30%, var(--silver-light) 52%, var(--silver-mid) 72%, var(--silver-dark) 100%);
  }
  .card-back .brand-mark {
    left: 0; right: 0; top: 135px; justify-content: center;
    font-size: 66px; color: var(--brand-grey-dark);
  }
  .card-back .brand-square { width: 56px; height: 56px; background: var(--brand-grey-dark); }
</style>
</head>
<body>

<section class="card card-front" aria-label="Visitenkarte Vorderseite">
  <svg class="front-bands" width="588" height="364" viewBox="0 0 588 364" aria-hidden="true">
    <defs>
      <linearGradient id="bandSheen" x1="0" y1="0" x2="0" y2="1">
        <stop offset="0" stop-color="#e2e2e2"/>
        <stop offset="1" stop-color="#b5b5b5"/>
      </linearGradient>
    </defs>
    <polygon points="0,188 402,188 380,218 0,218" fill="url(#bandSheen)"/>
    <polygon points="0,219 384,219 412,182 588,182 588,364 0,364" fill="var(--band-dark)"/>
  </svg>

  <div class="brand-mark"><span class="brand-square"></span><span>KVTL</span></div>

  <p class="holder-name">VORNAME NAME</p>

  <ul class="contact-list">
    <li>
      <svg viewBox="0 0 12 12" aria-hidden="true"><path fill="#fff" d="M2.4 1l2 2.2-1 1.3c.7 1.5 1.8 2.6 3.2 3.3l1.3-1 2.1 2-1.1 1.8C5 10.4 1.4 6.8 1 2.2z"/></svg>
      <span>07146-839214-0</span>
    </li>
    <li>
      <svg viewBox="0 0 12 12" aria-hidden="true"><rect x="1" y="2.5" width="10" height="7" fill="#fff"/><path d="M1 2.8l5 3.6 5-3.6" fill="none" stroke="#4f5052" stroke-width="1"/></svg>
      <span>Name@agentur-kvtl.de</span>
    </li>
    <li>
      <svg viewBox="0 0 12 12" aria-hidden="true"><circle cx="6" cy="6" r="4.8" fill="none" stroke="#fff" stroke-width="1.2"/><ellipse cx="6" cy="6" rx="2" ry="4.8" fill="none" stroke="#fff" stroke-width="1"/><path d="M1.2 6h9.6" stroke="#fff" stroke-width="1"/></svg>
      <span>www.agentur-kvtl.de</span>
    </li>
  </ul>

  <p class="address">Kellberger Str. 18 71409 Kernbach</p>
</section>

<section class="card card-back" aria-label="Visitenkarte Rückseite">
  <div class="brand-mark"><span class="brand-square"></span><span>KVTL</span></div>
</section>

</body>
</html>
```